Postcard Design

We are a small day care chain operating out of two adjacent homes. We need a design that illustrates a caring loving environment and focuses on the services we provide, our low weekly rates, and urge the receiver of the postcard to enroll now. Our services are: open 24 hours, Saturday care available, Camera surveillance system, small provider to student ratio, kindergarten preparedness program, tutoring, introduction to Spanish, music, art, gym, after school program, GPTA membership, transportation from and to home, school drop off and pick up, 3 meals and 3 snacks served daily. Our rates: starting as low as $78.22 a week and we accept PHB, employer, and military assistance. Certifications: State of Ohio licensed, Fenwick County trained and certified, KRBA trained. We are offering a wavier on the registration fee and space is limited. We would like are postcards to have the color shades of blue, green and yellow. Contact info: 555 210 4837 call for tour and visit us @ BrookHollowDayCare.example and on Facebook @ Brook Hollow Day Care. Location: across from the Corvell Playhouse. Serving ages 6 weeks to 12 years. These details must be noticeably displayed. Also our name Brook Hollow Day Care must be displayed on both sides.
Updates

We would like for the postcard to highlight our torturing pprogram and to say "ask about GPTA Membership"

Target Market(s)

young (ages 18-35)women with children

Industry/Entity Type

Environment

Requirements
Must have
• personality and character must stand out

```html
<!DOCTYPE html>
<html lang="en">
<head>
<meta charset="utf-8">
<title>Brook Hollow Day Care – Postcard</title>
<link href="https://fonts.googleapis.com/css2?family=Oswald:wght@500;600&family=Raleway:wght@300&family=Arimo:ital,wght@0,400;0,700;1,700&display=swap" rel="stylesheet">
<style>
  :root{
    --page:#ebebeb;
    --white:#ffffff;
    --teal:#1d7892;
    --teal-light:#2fa3bd;
    --teal-dark:#0e5169;
    --green:#6dbf2e;
    --green-dark:#4e9b1c;
    --yellow:#f4e510;
    --yellow-dark:#e0b800;
    --navy:#113e63;
    --ink-soft:#6b6b6b;
    --contact:#1f6e94;
  }
  *{box-sizing:border-box;margin:0;padding:0}
  html,body{width:1200px;height:848px;overflow:hidden;background:var(--page)}
  .canvas{position:relative;width:1200px;height:848px}

  .card{position:absolute;width:540px;height:417px;overflow:hidden;background:var(--white)}
  .card--front{left:55px;top:195px}
  .card--back{left:618px;top:253px;width:539px}

  .photo{position:absolute;left:0;top:0}
  .front-photo{width:540px;height:240px;
    background:linear-gradient(90deg,rgba(255,255,255,0) 45%,rgba(255,255,255,.9) 75%,#fff 100%),
               linear-gradient(180deg,#e6e1da 0%,#d6cfc6 45%,#c9b9a7 100%)}
  .waves{position:absolute;left:0;top:0}

  .brand-title{position:absolute;font-family:'Oswald',sans-serif;font-weight:600;line-height:1;white-space:nowrap}
  .front .brand-title{left:180px;top:22px;width:335px;text-align:right;font-size:30px;color:var(--green)}
  .tagline{position:absolute;font-family:'Raleway',sans-serif;font-weight:300;letter-spacing:1.5px;display:flex;align-items:center;gap:8px;white-space:nowrap}
  .tagline::before,.tagline::after{content:"";height:1px;width:44px;background:currentColor}
  .front .tagline{left:248px;top:59px;font-size:12.5px;color:var(--ink-soft)}

  .badge{position:absolute;border-radius:50%;display:flex;align-items:center;justify-content:center;text-align:center;
    font-family:'Arimo',sans-serif;font-weight:700;line-height:1.05}
  .badge::after{content:"";position:absolute;inset:4px;border:1px dashed rgba(255,255,255,.85);border-radius:50%}
  .badge--rate{left:405px;top:124px;width:90px;height:90px;background:var(--green);color:var(--white);font-size:8.5px;padding:12px}

  .ribbon{position:absolute;height:24px;background:var(--yellow);font-family:'Oswald',sans-serif;font-weight:600;color:var(--navy);
    font-size:19px;line-height:24px;padding-left:10px;clip-path:polygon(0 0,100% 0,93% 50%,100% 100%,0 100%)}
  .ribbon::before{content:"";position:absolute;left:-14px;top:5px;width:14px;height:24px;background:var(--yellow-dark)}
  .ribbon-wrap{position:absolute}
  .front .ribbon-wrap{left:17px;top:203px}
  .front .ribbon{position:relative;width:143px}

  .services{position:absolute;list-style:none;font-family:'Arimo',sans-serif;font-size:10.8px;line-height:11.6px;color:var(--white)}
  .services li{position:relative;padding-left:13px}
  .services li::before{content:"";position:absolute;left:2px;top:3.5px;width:5px;height:5px;border-radius:50%;background:var(--white)}
  .services .highlight{font-style:italic;font-weight:700}
  .services--left{left:31px;top:240px;width:220px}
  .services--right{left:246px;top:240px;width:270px}

  .front-details{position:absolute;left:31px;top:318px;width:262px;font-family:'Arimo',sans-serif;font-weight:700;font-size:9.5px;line-height:12px;color:var(--yellow)}

  .cta{position:absolute;left:300px;top:320px;width:240px;height:26px;
    background:linear-gradient(90deg,rgba(47,163,189,0) 0%,var(--teal-light) 35%);
    font-family:'Oswald',sans-serif;font-weight:600;font-size:18px;line-height:26px;color:var(--white);text-align:right;padding-right:27px}

  .contact-bar{position:absolute;left:0;height:38px;width:100%;background:var(--white);display:flex;align-items:center}
  .card--front .contact-bar{top:352px;padding:0 20px;justify-content:space-between}
  .contact-item{display:flex;align-items:center;gap:5px;font-family:'Oswald',sans-serif;font-weight:500;font-size:15px;color:var(--contact);white-space:nowrap}
  .dot{width:23px;height:23px;border-radius:50%;background:var(--contact);display:flex;align-items:center;justify-content:center;flex:none}
  .dot svg{width:13px;height:13px}
  .footer-band{position:absolute;left:0;bottom:0;width:100%;height:27px;background:var(--teal)}

  .back-panel{position:absolute;left:0;top:0;width:262px;height:417px;overflow:hidden}
  .back-photo{width:262px;height:215px;background:linear-gradient(160deg,#e9c45a 0%,#d7a84b 35%,#c9b7a3 70%,#b9a898 100%)}
  .back .brand-title{left:0;top:20px;width:262px;text-align:center;font-size:26px;color:var(--white)}
  .back .tagline{left:48px;top:51px;font-size:11px;color:var(--white)}
  .back .tagline::before,.back .tagline::after{width:20px}
  .badge--promise{left:163px;top:154px;width:78px;height:78px;background:var(--yellow);color:var(--navy);font-size:8.5px;padding:10px}
  .badge--promise::after{border-color:rgba(17,62,99,.6)}
  .back .ribbon-wrap{left:20px;top:245px}
  .back .ribbon{position:relative;width:137px}
  .cert-list{position:absolute;left:32px;top:276px;font-family:'Arimo',sans-serif;font-weight:700;font-size:12.5px;line-height:17px;color:var(--white);white-space:nowrap}
  .enroll-note{position:absolute;left:32px;top:331px;width:225px;font-family:'Arimo',sans-serif;font-weight:700;font-size:9.5px;line-height:11px;color:var(--yellow)}
  .card--back .contact-bar{top:358px;width:262px;justify-content:flex-end;padding-right:14px;gap:5px}
  .contact-label{font-family:'Arimo',sans-serif;font-weight:700;font-size:8px;line-height:9px;color:var(--contact);text-align:right}
  .card--back .dot{width:30px;height:30px}
  .card--back .dot svg{width:16px;height:16px}
  .phone-large{font-family:'Oswald',sans-serif;font-weight:500;font-size:21px;color:var(--contact)}
  .card--back .footer-band{width:262px;height:22px}
  .address-area{position:absolute;left:262px;top:0;width:277px;height:417px;background:#f7f7f7}
</style>
</head>
<body>
<main class="canvas">

  <section class="card card--front front">
    <div class="photo front-photo" role="img" aria-label="Photo of a smiling teacher exploring a globe with a child in a bright classroom"></div>
    <svg class="waves" width="540" height="417" viewBox="0 0 540 417" aria-hidden="true">
      <defs>
        <radialGradient id="frontTeal" cx="0.5" cy="0.6" r="0.7">
          <stop offset="0" stop-color="#2fa3bd"/>
          <stop offset="0.6" stop-color="#1d7892"/>
          <stop offset="1" stop-color="#0e5169"/>
        </radialGradient>
      </defs>
      <path d="M0 165 C160 225 360 220 540 75 L540 140 C360 240 150 240 0 185 Z" fill="#f4e510"/>
      <path d="M0 128 C110 195 250 212 380 204 C250 226 110 218 0 182 Z" fill="#6dbf2e"/>
      <path d="M0 183 C150 238 360 238 540 138 L540 417 L0 417 Z" fill="url(#frontTeal)"/>
    </svg>

    <h1 class="brand-title">Brook Hollow Day Care</h1>
    <p class="tagline">home day care service</p>

    <div class="badge badge--rate">Starting as low as $78.22 a week and we accept PHB, employer, and military assistance</div>

    <div class="ribbon-wrap"><h2 class="ribbon">Our services</h2></div>

    <ul class="services services--left">
      <li>Open 24 hours.</li>
      <li>Saturday care available.</li>
      <li>Camera surveillance system.</li>
      <li>Small provider to student ratio.</li>
      <li>kindergarten preparedness program.</li>
      <li>Tutoring, introduction to Spanish.</li>
    </ul>
    <ul class="services services--right">
      <li>Music, art, gym.</li>
      <li class="highlight">After school program.</li>
      <li class="highlight">GPTA membership.</li>
      <li>Transportation from and to home, school drop off and pick up.</li>
      <li>3 meals and 3 snacks served daily.</li>
    </ul>

    <p class="front-details">Serving ages 6 weeks to 12 years.<br>Across from the Corvell Playhouse.</p>

    <p class="cta">CALL FOR A TOUR TODAY!</p>

    <div class="contact-bar">
      <span class="contact-item"><span class="dot"></span>Brook Hollow Day Care</span>
      <span class="contact-item"><span class="dot"></span>BrookHollowDayCare.example</span>
      <span class="contact-item"><span class="dot">
        <svg viewBox="0 0 24 24" aria-hidden="true"><path fill="#fff" d="M6.6 10.8a15.1 15.1 0 0 0 6.6 6.6l2.2-2.2a1 1 0 0 1 1-.25 11.4 11.4 0 0 0 3.6.57 1 1 0 0 1 1 1V20a1 1 0 0 1-1 1A17 17 0 0 1 3 4a1 1 0 0 1 1-1h3.5a1 1 0 0 1 1 1c0 1.250.2 2.450.57 3.57a1 1 0 0 1-.25 1Z"/></svg>
      </span>555 210 4837</span>
    </div>
    <div class="footer-band"></div>
  </section>

  <section class="card card--back back">
    <div class="back-panel">
      <div class="photo back-photo" role="img" aria-label="Photo of toddlers playing with toys at a classroom table"></div>
      <svg class="waves" width="262" height="417" viewBox="0 0 262 417" aria-hidden="true">
        <defs>
          <radialGradient id="backTeal" cx="0.45" cy="0.55" r="0.75">
            <stop offset="0" stop-color="#2fa3bd"/>
            <stop offset="0.6" stop-color="#1d7892"/>
            <stop offset="1" stop-color="#0e5169"/>
          </radialGradient>
        </defs>
        <path d="M0 180 C90 228 190 205 262 122 L262 165 C190 225 80 240 0 205 Z" fill="#f4e510"/>
        <path d="M0 203 C80 238 190 222 262 160 L262 417 L0 417 Z" fill="url(#backTeal)"/>
      </svg>

      <h2 class="brand-title">Brook Hollow Day Care</h2>
      <p class="tagline">home day care service</p>

      <div class="badge badge--promise">parents are paying for quality services and not a building and staff</div>

      <div class="ribbon-wrap"><h3 class="ribbon">Certifications</h3></div>
      <p class="cert-list">State of Ohio licensed,<br>Fenwick County trained and certified,<br>KRBA trained.</p>
      <p class="enroll-note">Enroll now – registration fee waived. Space is limited!</p>

      <div class="contact-bar">
        <span class="contact-label">CONTACT<br>INFO</span>
        <span class="dot">
          <svg viewBox="0 0 24 24" aria-hidden="true"><path fill="#fff" d="M6.6 10.8a15.1 15.1 0 0 0 6.6 6.6l2.2-2.2a1 1 0 0 1 1-.25 11.4 11.4 0 0 0 3.6.57 1 1 0 0 1 1 1V20a1 1 0 0 1-1 1A17 17 0 0 1 3 4a1 1 0 0 1 1-1h3.5a1 1 0 0 1 1 1c0 1.250.2 2.450.57 3.57a1 1 0 0 1-.25 1Z"/></svg>
        </span>
        <span class="phone-large">555 210 4837</span>
      </div>
      <div class="footer-band"></div>
    </div>
    <div class="address-area"></div>
  </section>

</main>
</body>
</html>
```